Quarrybend Marble & Tile Needs a Business Card

Attached you will find your logo, my photo and design guidelines for a new business card. The final design will need two separate files to create an embossed card. The cards will be printed by www.plinkprint.com (Instructions below)
Format is the Plink SQUARE card
Quarrybend Marble And Tile is a brick and mortar, retail stone and tile shop.
One the front:
Quarrybend Marble And Tile
Dorian Fesslock
Owner
24807 Hollis Verdant Blvd
Suite P & R
Charlotte, NC 28193
Cell: 704-583-7142
Web: www.QuarrybendMarbleAndTile.com
(Make each word of the domain a different or alternating color)
On the back;
Something that shows beautiful colorful tile
Follow the design guide closely please. For more information see this page that describes creating the spot gloss file: https://www.plinkprint.com/us/business-cards/design-guidelines-spot-gloss
The logo is what we would like to have raised spot glossed.
Format is the Plink SQUARE card. See attahced guidlines.

```html
<!DOCTYPE html>
<html lang="en">
<head>
<meta charset="utf-8">
<title>Quarrybend Marble &amp; Tile — Business Card</title>
<link rel="stylesheet" href="https://fonts.googleapis.com/css2?family=Cinzel:wght@400&family=Tinos&family=Arimo:wght@400;700&display=swap">
<style>
  :root {
    --backdrop: #b3b4b6;
    --ink-navy: #22323d;
    --rust: #b0482a;
    --ochre: #b57a2c;
    --gold-line: #c79a5e;
    --paper: #ececec;
    --slate: #4b5b66;
    --sage: #6f7a5c;
    --sand: #c8b9a6;
  }
  * { margin: 0; padding: 0; box-sizing: border-box; }
  html, body { width: 1200px; height: 1000px; overflow: hidden; }
  body { background: var(--backdrop); position: relative; font-family: "Arimo", Arial, sans-serif; }

  .card { position: absolute; overflow: hidden; }
  .card-front { left: 343px; top: 152px; width: 512px; height: 321px; }
  .card-back { left: 343px; top: 544px; width: 514px; height: 324px; background: var(--paper); }

  .tile-field {
    position: absolute; inset: 0;
    background: linear-gradient(135deg, var(--ink-navy) 0%, var(--slate) 35%, var(--rust) 55%, var(--sage) 75%, var(--ink-navy) 100%);
  }
  .medallion { position: absolute; inset: 0; }

  .wordmark { font-family: "Cinzel", "Times New Roman", serif; color: var(--ink-navy); font-weight: 400; text-align: center; }

  .contact-panel { position: absolute; left: 0; top: 0; width: 276px; height: 100%; text-align: center; }
  .contact-panel .mark-square { position: absolute; left: 128px; top: 36px; width: 22px; height: 22px; background: var(--rust); }
  .contact-panel .wordmark-main { position: absolute; left: 0; right: 0; top: 76px; font-size: 19px; letter-spacing: 1.5px; }
  .contact-panel .wordmark-sub { position: absolute; left: 0; right: 0; top: 100px; font-size: 8px; letter-spacing: 2.5px; }

  .person-name { position: absolute; left: 0; right: 0; top: 127px; font-family: "Tinos", "Times New Roman", serif; font-size: 17px; color: var(--ink-navy); }
  .person-title { position: absolute; left: 0; right: 0; top: 150px; font-family: "Tinos", "Times New Roman", serif; font-size: 16px; color: var(--rust); }
  .divider { position: absolute; left: 58px; top: 179px; width: 160px; height: 1px; background: var(--gold-line); }
  .divider-gem { position: absolute; left: 135px; top: 176px; width: 6px; height: 6px; background: var(--ochre); transform: rotate(45deg); }
  .phone { position: absolute; left: 0; right: 0; top: 191px; font-size: 13px; color: var(--ink-navy); }
  .phone b { color: var(--rust); }
  .address { position: absolute; left: 0; right: 0; top: 222px; font-size: 11px; line-height: 14px; color: var(--ink-navy); }
  .website { position: absolute; left: 0; right: 0; top: 279px; font-size: 13px; color: var(--ink-navy); }
  .website .w-ochre { color: var(--ochre); font-weight: 700; }
  .website .w-navy { color: var(--ink-navy); font-weight: 700; }
  .website .w-rust { color: var(--rust); font-weight: 700; }

  .portrait {
    position: absolute; left: 275px; top: 0; width: 239px; height: 100%;
    background: linear-gradient(160deg, var(--rust) 0%, var(--sand) 30%, var(--slate) 60%, var(--ink-navy) 100%);
  }
</style>
</head>
<body>

  <section class="card card-front">
    <div class="tile-field" role="img" aria-label="Colourful mosaic of triangular stone tiles in rust, sage, slate and sand"></div>
    <svg class="medallion" width="512" height="321" viewBox="0 0 512 321">
      <g transform="translate(257 160)">
        <polygon fill="#ececec" points="0,-141 41,-100 100,-100 100,-41 141,0 100,41 100,100 41,100 0,141 -41,100 -100,100 -100,41 -141,0 -100,-41 -100,-100 -41,-100"/>
        <polygon fill="none" stroke="#c79a5e" stroke-width="1.2" transform="scale(0.94)" points="0,-141 41,-100 100,-100 100,-41 141,0 100,41 100,100 41,100 0,141 -41,100 -100,100 -100,41 -141,0 -100,-41 -100,-100 -41,-100"/>
        <rect x="-14" y="-82" width="28" height="28" fill="#b0482a"/>
        <text class="wordmark" x="0" y="18" text-anchor="middle" font-family="Cinzel, serif" font-size="24" letter-spacing="2" fill="#22323d">QUARRYBEND</text>
        <text class="wordmark" x="0" y="42" text-anchor="middle" font-family="Cinzel, serif" font-size="11" letter-spacing="3.5" fill="#22323d">MARBLE &amp; TILE</text>
      </g>
    </svg>
  </section>

  <section class="card card-back">
    <div class="contact-panel">
      <div class="mark-square"></div>
      <div class="wordmark wordmark-main">QUARRYBEND</div>
      <div class="wordmark wordmark-sub">MARBLE &amp; TILE</div>
      <div class="person-name">Dorian Fesslock</div>
      <div class="person-title">Owner</div>
      <div class="divider"></div>
      <div class="divider-gem"></div>
      <div class="phone"><b>Cell:</b> 704-583-7142</div>
      <div class="address">24807 Hollis Verdant Blvd<br>Suite P &amp; R<br>Charlotte, NC 28193</div>
      <div class="website"><span class="w-ochre">Quarrybend</span><span class="w-navy">Marble</span><span class="w-rust">And</span><span class="w-navy">Tile</span>.com</div>
    </div>
    <div class="portrait" role="img" aria-label="Portrait photo of the owner in a checked blazer, set over a mosaic tile backdrop"></div>
  </section>

</body>
</html>
```